QUORVIN CAPABILITY STATEMENT “Shaping Lasting Links”

QUORVIN CAPABILITY STATEMENT
“Shaping Lasting Links”
Indigenous-Owned Telecommunications & Infrastructure Solutions Partner

COVER PAGE

Visual: Modern and clean design featuring telecom towers, wind turbines, civil infrastructure, roads, and community WiFi imagery.
Tagline: “Linking Places, Lifting Futures.”
Contact:
Website: www.quorvin.com.au
Email: info@quorvin.com.au
Phone: [Insert Main Number]
“Proudly Indigenous-Owned | Compliant with Aboriginal Procurement Policy (APP) & SME Policies”
INTRODUCTION

Quorvin is a 100% Indigenous-owned leader in comprehensive infrastructure solutions, specializing in telecommunications, civil works, renewable energy, structural engineering, and site development. With over a decade of experience, we deliver safe, reliable, and culturally respectful services across Australia, from urban centers to remote wind farms and heritage sites. Our mission: “To bridge infrastructure gaps while empowering Indigenous communities and fostering sustainable growth.”

CORE CAPABILITIES

TELECOMMUNICATIONS

Tower Builds & Maintenance: Structural engineering, geotechnical analysis, foundation mapping.
Community WiFi Projects: Enhancing digital inclusion in Indigenous and remote communities.
Fiber & Wireless Networks: End-to-end installation for Velonet, Satellite, and regional connectivity.
Height Safety Systems: Design, inspection, and certification of fall-arrest safety infrastructure.
CIVIL & STRUCTURAL ENGINEERING

Foundations & Concreting: Reinforced slabs, grillage, geotech-to-construction turnkey solutions.
Site Development: Earthworks, drainage, and access road/track construction.
Wind Farm Infrastructure: Reinforcing towers and integrating power systems for high-wind environments.
ROAD & ACCESS TRACK CONSTRUCTION

Construction of durable access roads and tracks: For remote projects and urban settings.
Remediation of existing tracks: Upgrading for environmental compliance and sustainability.
Facilitating logistics and site access: Particularly in challenging terrain.
POWER & ELECTRICAL SYSTEMS

Off-grid energy solutions: Solar hybrid systems, electrical structural engineering.
Grid upgrades: Ensuring compliance with AS/NZS standards and facilitating connection upgrades.
SITE REFURBISHMENT & DEMOLITION

Comprehensive refurbishment and demolition services: For outdated telecom sites and structures.
Environmentally responsible dismantling: Focused on recycling materials and minimizing land impact.
EMERGENCY RESPONSE SERVICES

24/7 Rapid Response: Over 450 callouts annually; 4,000+ emergencies resolved nationwide.
Disaster Recovery: Comprehensive support during floods, bushfires for Velonet, Marvaske, Trilumen, and regional clients.
PROJECT EXPERIENCE

Heritage Tower Upgrade

Enhanced safety and technology on culturally significant heritage sites, preserving their integrity.
Wind Farm Deployment

Delivered power, fiber, and reinforced foundations for large-scale renewable energy projects in high-wind environments.
Regional Fibre Network

Laid 200km of fiber in flood-prone regions, ensuring critical infrastructure resilience.
Indigenous Community WiFi & Connectivity

Installed sustainable WiFi networks to bridge the digital divide, supporting education, health, and business activities.
Site Demolition & Refurbishment

Safely decommissioned aging telecom sites and structures across Australia, emphasizing land reuse and environmental care.
Access Track Construction & Remediation

Developed new access roads and refurbished existing tracks to facilitate project logistics, particularly in remote or environmentally sensitive areas.
Key Stats:
+600 sites supported | 10-year Velonet partner | 98% client retention | Over 20 Indigenous community WiFi deployments

COMMITMENT TO SAFETY & QUALITY

“Pause Twice, Work Wise” Protocol: Enforced pre-task risk assessments to ensure safety at every stage.
Certifications: ISO 45001 (Safety) | ISO 9001 (Quality Management).
Safety Culture: Regular safety audits, Indigenous-led training programs, and safety initiatives focused on community well-being.
INDIGENOUS INCLUSION & COMMUNITY IMPACT

Elders Guidance Council: Provides guidance on community engagement, cultural sensitivity, and social responsibility.
Supplier Diversity: 30% procurement from Indigenous-owned businesses, fostering economic growth.
Regional Employment: 65% of our workforce originates from local communities, creating sustainable jobs.
Testimonial: “Quorvin’s partnership empowered our community with jobs and infrastructure that respects our land.” – Local Indigenous Leader

CONTACT & SERVICE AREAS

Headquarters: [Insert Address] | ABN: [Insert ABN]

24/7 Emergency Support: [Insert Dedicated Emergency Line]

Certifications & Registrations:

Trade Circle Registered, First Enterprise Register (FER)
SERVICE AREAS

National Coverage with Regional Expertise:
Major Cities: Sydney, Melbourne, Brisbane, Perth, Adelaide, Darwin, Hobart.
Regional & Remote Areas: Pilbara, Kimberley, Far North Queensland, Outback NSW.
Disaster Zones: Rapid response teams deployed nationwide for bushfire and flood incidents.
EMERGENCY SUPPORT

SLA Guarantee: 90% of emergencies addressed within 4 hours.
Partners Supported: Velonet, Marvaske, Trilumen, regional councils.
This capability statement reflects our commitment to quality, safety, and community engagement across all levels of operation, ensuring that we empower the communities we serve while maintaining the highest standards of service delivery.

Target Market(s)

Government Agencies: Especially those seeking to comply with Indigenous Procurement Policies. Telecommunication Operators: Such as Velonet, Marvaske, and Trilumen for infrastructure deployment. Indigenous Communities: Projects aimed at enhancing connectivity and digital inclusion. Utilities and Energy Providers: For power and electrical infrastructure projects. Construction and Engineering Firms: Seeking collaboration on civil and structural infrastructure projects.

Industry/Entity Type

Telecommunications and Infrastructure Development: Focused on service delivery in various contexts, including urban settings, remote locations, and Indigenous community projects. Renewable Energy: This includes wind and solar infrastructure linked to telecommunications enhancements. Civil Engineering: Related to building and maintaining essential infrastructure such as access roads and utility lines.

Font styles to use
Other font styles liked:
• Bubbleboddy neue

Requirements
Must have
• Clear demonstration of Indigenous ownership and community engagement. Compliance with relevant safety and quality certifications (e.g., ISO 45001, ISO 9001). Showcase of core capabilities in telecommunications, civil engineering, and those specific to renewable energy. Visuals that reflect the diverse range of services offered (like telecom towers and community WiFi installations).
Nice to have
• Interactive elements such as hyperlinks to project case studies or client testimonials. Infographics or visual data to highlight key statistics and project success rates. Cultural motifs or imagery that reflect Indigenous heritage and inclusion in design aspirations. QR codes that link to videos or more detailed project descriptions for digital formats.
Should not have
• Clutter or excessive text that detracts from the main messages. Generic stock images that don’t align with the specific projects or Indigenous culture. Technical jargon that could confuse stakeholders unfamiliar with industry-specific terms. Overemphasis on competitors; the focus should remain on Quorvin's unique strengths and contributions.

```html
<!DOCTYPE html>
<html lang="en">
<head>
<meta charset="utf-8">
<title>Quorvin Capability Statement – Introduction &amp; Core Capabilities</title>
<link href="https://fonts.googleapis.com/css2?family=Montserrat:wght@300;400;500;600;700&display=swap" rel="stylesheet">
<style>
  :root{
    --red:#e8282d;
    --red-dark:#c81d22;
    --red-mid:#f04046;
    --red-soft:#f36b6e;
    --red-pale:#f47c7e;
    --ink:#1a1a1a;
    --body:#3a3a3a;
    --row-bg:#f4f4f4;
    --page:#ffffff;
    --divider:#e6e6e6;
  }
  *{margin:0;padding:0;box-sizing:border-box;}
  html,body{width:1200px;height:842px;overflow:hidden;background:var(--page);}
  body{font-family:"Montserrat",sans-serif;color:var(--body);position:relative;}

  .spread{position:absolute;inset:0;display:flex;}
  .page{position:relative;width:600px;height:842px;background:var(--page);}
  .page--left{border-right:1px solid var(--divider);}

  /* headings */
  .section-title{position:absolute;left:45px;top:48px;font-weight:700;font-size:14px;color:var(--ink);letter-spacing:.3px;padding-left:10px;line-height:16px;}
  .section-title::before{content:"";position:absolute;left:0;top:1px;width:4px;height:13px;background:var(--red);}

  .stacked-title{position:absolute;left:45px;padding-left:14px;color:var(--ink);line-height:1.15;}
  .stacked-title::before{content:"";position:absolute;left:0;top:2px;width:5px;bottom:2px;background:var(--red);}
  .stacked-title .light{display:block;font-weight:400;font-size:14.8px;}
  .stacked-title .bold{display:block;font-weight:700;font-size:14.8px;}

  .body-text{position:absolute;left:45px;width:510px;font-weight:300;font-size:11.3px;line-height:19px;text-align:justify;color:var(--body);}
  .intro-text{top:84px;}
  .mission-text{top:670px;}

  /* photo with frame corners */
  .frame-corner{position:absolute;border:0 solid var(--red);}
  .frame-corner--tl{left:45px;top:246px;width:105px;height:69px;border-top-width:10px;border-left-width:10px;}
  .frame-corner--br{left:450px;top:475px;width:105px;height:69px;border-bottom-width:10px;border-right-width:10px;}
  .photo{position:absolute;left:55px;top:256px;width:490px;height:278px;background:linear-gradient(160deg,#8cc6d8 0%,#5aa3bf 35%,#c9c1b0 62%,#e07a34 82%,#b9c34f 100%);}

  .mission-title{top:610px;}

  /* footer */
  .footer{position:absolute;left:45px;top:786px;width:510px;height:14px;display:flex;align-items:center;}
  .footer-brand{font-weight:500;font-size:9.5px;color:var(--ink);letter-spacing:.2px;margin-right:8px;}
  .footer-rule{flex:1;height:1px;background:var(--red);position:relative;}
  .footer-rule::before{content:"";position:absolute;left:0;top:-1px;width:36px;height:2px;background:var(--ink);}
  .page-number{width:14px;height:14px;background:var(--red);color:#fff;font-weight:700;font-size:8.5px;display:flex;align-items:center;justify-content:center;}

  /* capabilities */
  .cap-title{top:46px;}
  .cap-group{position:absolute;left:44px;width:511px;}
  .cap-group h3{font-weight:700;font-size:13.6px;color:var(--red);letter-spacing:.1px;line-height:16px;margin-bottom:10px;}
  .cap-row{display:flex;align-items:center;height:35px;background:var(--row-bg);margin-bottom:10.7px;}
  .cap-label{flex:0 0 124px;height:100%;display:flex;align-items:center;padding:0 16px 0 8px;color:#fff;font-weight:600;font-size:10.7px;line-height:1.2;clip-path:polygon(0 0,90% 0,100% 50%,90% 100%,0 100%);}
  .cap-label--compact{font-size:9.2px;padding-right:12px;}
  .cap-desc{padding-left:9px;padding-right:6px;font-weight:400;font-size:10.5px;line-height:1.2;color:var(--ink);}

  .cap-group--telecom{top:105px;}
  .cap-group--telecom .cap-label{background:linear-gradient(180deg,var(--red) 0%,var(--red-dark) 100%);}
  .cap-group--civil{top:324px;}
  .cap-group--civil .cap-label{background:var(--red-mid);}
  .cap-group--road{top:499px;}
  .cap-group--road .cap-label{background:var(--red-soft);}
  .cap-group--power{top:673px;}
  .cap-group--power .cap-label{background:var(--red-pale);}
</style>
</head>
<body>
<div class="spread">

  <section class="page page--left">
    <h2 class="section-title">INTRODUCTION</h2>
    <p class="body-text intro-text">Quorvin is a 100% Indigenous-owned leader in comprehensive infrastructure solutions, specializing in telecommunications, civil works, renewable energy, structural engineering, and site development. With over a decade of experience, we deliver safe, reliable, and culturally respectful services across Australia, from urban centers to remote wind farms and heritage sites.</p>

    <div class="frame-corner frame-corner--tl"></div>
    <div class="frame-corner frame-corner--br"></div>
    <div class="photo" role="img" aria-label="Photo: construction workers in hard hats and hi-vis vests looking at a scaffolded building under a tower crane"></div>

    <h2 class="stacked-title mission-title"><span class="light">Our</span><span class="bold">Mission</span></h2>
    <p class="body-text mission-text">To bridge infrastructure gaps while empowering Indigenous communities and fostering sustainable growth.</p>

    <footer class="footer">
      <span class="footer-brand">QUORVIN</span>
      <span class="footer-rule"></span>
      <span class="page-number">2</span>
    </footer>
  </section>

  <section class="page page--right">
    <h2 class="stacked-title cap-title"><span class="light">CORE</span><span class="bold">CAPABILITIES</span></h2>

    <div class="cap-group cap-group--telecom">
      <h3>TELECOMMUNICATIONS</h3>
      <div class="cap-row"><div class="cap-label">Tower Builds &amp; Maintenance:</div><div class="cap-desc">Structural engineering, geotechnical analysis, foundation mapping.</div></div>
      <div class="cap-row"><div class="cap-label">Community WiFi Projects:</div><div class="cap-desc">Enhancing digital inclusion in Indigenous and remote communities.</div></div>
      <div class="cap-row"><div class="cap-label">Fiber &amp; Wireless Networks:</div><div class="cap-desc">End-to-end installation for Velonet, Satellite, and regional connectivity.</div></div>
      <div class="cap-row"><div class="cap-label">Height Safety Systems:</div><div class="cap-desc">Design, inspection, and certification of fall-arrest safety infrastructure.</div></div>
    </div>

    <div class="cap-group cap-group--civil">
      <h3>CIVIL &amp; STRUCTURAL ENGINEERING</h3>
      <div class="cap-row"><div class="cap-label">Foundations &amp; Concreting:</div><div class="cap-desc">Reinforced slabs, grillage, geotech-to-construction turnkey solutions.</div></div>
      <div class="cap-row"><div class="cap-label">Site Development:</div><div class="cap-desc">Earthworks, drainage, and access road/track construction.</div></div>
      <div class="cap-row"><div class="cap-label">Wind Farm Infrastructure:</div><div class="cap-desc">Reinforcing towers and integrating power systems for high-wind environments.</div></div>
    </div>

    <div class="cap-group cap-group--road">
      <h3>ROAD &amp; ACCESS TRACK CONSTRUCTION</h3>
      <div class="cap-row"><div class="cap-label">Constructions Durability</div><div class="cap-desc">Construction of durable access roads and tracks - For remote projects and urban settings.</div></div>
      <div class="cap-row"><div class="cap-label">Remediation of existing tracks:</div><div class="cap-desc">Upgrading for environmental compliance and sustainability.</div></div>
      <div class="cap-row"><div class="cap-label cap-label--compact">Facilitating logistics &amp; site access</div><div class="cap-desc">Particularly in challenging terrain.</div></div>
    </div>

    <div class="cap-group cap-group--power">
      <h3>POWER &amp; ELECTRICAL SYSTEMS</h3>
      <div class="cap-row"><div class="cap-label">Off-grid Energy Solutions:</div><div class="cap-desc">Solar hybrid systems, electrical structural engineering.</div></div>
      <div class="cap-row"><div class="cap-label">Grid Upgrades:</div><div class="cap-desc">Ensuring compliance with AS/NZS standards and facilitating connection upgrades.</div></div>
    </div>

    <footer class="footer">
      <span class="footer-brand">QUORVIN</span>
      <span class="footer-rule"></span>
      <span class="page-number">3</span>
    </footer>
  </section>

</div>
</body>
</html>
```